Facebook Cover Photo & Mailchimp Template for Greyhound Racing Club

Create a consistent, professional visual identity across Facebook and email communications that promotes PWTA as a modern, community-focused greyhound racing club while respecting the heritage of greyhound racing.
Include PWTA logo.
Existing site https://www.socialpage-example.com/WestmereRunners/

```html
<!DOCTYPE html>
<html lang="en">
<head>
<meta charset="utf-8">
<title>PWTA Facebook Cover</title>
<link rel="stylesheet" href="https://fonts.googleapis.com/css2?family=Poppins:wght@400;700&display=swap">
<style>
  :root {
    --page-bg: #eceef1;
    --cover-bg: #ffffff;
    --club-green: #169a14;
    --ink: #000000;
    --paper: #ffffff;
    --photo-warm: #a8876a;
    --photo-blue: #4a72d6;
    --photo-red: #d9363a;
  }
  * { margin: 0; padding: 0; box-sizing: border-box; }
  html, body {
    width: 1200px;
    height: 600px;
    overflow: hidden;
    background: var(--page-bg);
    font-family: "Poppins", sans-serif;
  }
  .cover {
    position: absolute;
    left: 0;
    top: 78px;
    width: 1200px;
    height: 444px;
    background: var(--cover-bg);
    overflow: hidden;
  }
  .cover-shapes {
    position: absolute;
    inset: 0;
    width: 100%;
    height: 100%;
  }
  .club-mark {
    position: absolute;
    left: 50px;
    top: 44px;
    display: flex;
    align-items: center;
    gap: 12px;
  }
  .club-mark-dot {
    width: 30px;
    height: 30px;
    border-radius: 50%;
    background: var(--club-green);
  }
  .club-mark-name {
    font-size: 34px;
    font-weight: 700;
    color: var(--ink);
    letter-spacing: 2px;
    line-height: 1;
  }
  .club-site {
    position: absolute;
    right: 52px;
    top: 38px;
    font-size: 21px;
    font-weight: 400;
    color: var(--paper);
    letter-spacing: 0.3px;
  }
  .headline {
    position: absolute;
    right: 52px;
    top: 232px;
    text-align: right;
    font-size: 42px;
    font-weight: 700;
    line-height: 48px;
    color: var(--ink);
  }
  .headline .accent { color: var(--club-green); }
</style>
</head>
<body>
  <section class="cover">
    <svg class="cover-shapes" viewBox="0 0 1200 444" preserveAspectRatio="none">
      <defs>
        <linearGradient id="photoTone" x1="0" y1="0" x2="1" y2="1">
          <stop offset="0" stop-color="var(--photo-warm)"/>
          <stop offset="0.35" stop-color="var(--photo-blue)"/>
          <stop offset="0.55" stop-color="var(--photo-red)"/>
          <stop offset="1" stop-color="var(--photo-warm)"/>
        </linearGradient>
      </defs>
      <rect class="dog-photo" role="img" aria-label="Photo of two racing greyhounds in blue and red rugs sprinting forward"
            x="0" y="110" width="680" height="334" rx="0" fill="url(#photoTone)"/>
      <polygon class="band-black" fill="var(--ink)" points="760,0 1200,0 1200,150 660,100"/>
      <polygon class="band-green" fill="var(--club-green)" points="640,110 1200,168 1200,196 610,138"/>
      <polygon class="band-green-low" fill="var(--club-green)" points="0,430 680,400 680,412 0,444"/>
    </svg>

    <div class="club-mark">
      <span class="club-mark-dot"></span>
      <span class="club-mark-name">PWTA</span>
    </div>

    <p class="club-site">westmererunners.com.au</p>

    <h1 class="headline">
      <span class="accent">Watch</span> Every<br>
      Victorian <span class="accent">Greyhound</span><br>
      Race Live
    </h1>
  </section>
</body>
</html>
```